Brand Identity Stationary Package

Hello I'm looking for a full branding package for my Property Management Company. I have a logo but looking to have the following
Business Card
Email signature
Facebook cover photo
Letterhead (word.doc)
#10 Envelope
Pocket Folder - link to 9x12 pocket folder design specs https://www.printorbit-example.ca/marketing-materials/presentation-folders
would like everything to match and be brand identifiable. The company looks after residential properties/apartments and some commercial properties. Attached is a zip of the files.
For Business Card
Name: Gareth Lindqvist
Position: Operations Manager
Number: 1 (555) 384-2917
Email: Gareth@harborkey-example.ca
Website: Harborkey-example.ca
Property Management

```html
<!DOCTYPE html>
<html lang="en">
<head>
<meta charset="utf-8">
<title>Harborkey Letterhead</title>
<link rel="stylesheet" href="https://fonts.googleapis.com/css2?family=Figtree:wght@400;500;700&family=Montserrat:wght@700&display=swap">
<style>
  :root {
    --green: #82ab3a;
    --green-deep: #6f9630;
    --ink: #111111;
    --backdrop: #e8e8e8;
    --paper: #ffffff;
  }
  * { margin: 0; padding: 0; box-sizing: border-box; }
  html, body {
    width: 1154px;
    height: 1200px;
    overflow: hidden;
    background: var(--backdrop);
  }
  .letterhead {
    position: absolute;
    left: 174px;
    top: 30px;
    width: 806px;
    height: 1140px;
    background: var(--paper);
    overflow: hidden;
    font-family: "Figtree", sans-serif;
    color: var(--ink);
  }
  .brand-name {
    position: absolute;
    left: 61px;
    top: 52px;
    font-family: "Montserrat", sans-serif;
    font-weight: 700;
    font-size: 42px;
    letter-spacing: 4px;
    line-height: 1;
    color: var(--ink);
  }
  .contact-block {
    position: absolute;
    left: 520px;
    top: 49px;
    height: 110px;
    border-left: 1.5px solid var(--green);
    padding-left: 15px;
  }
  .contact-name {
    font-weight: 700;
    font-size: 17px;
    color: var(--green);
    letter-spacing: 0.2px;
    line-height: 1;
    margin-top: -4px;
  }
  .contact-role {
    font-size: 15.5px;
    margin-top: 4px;
    line-height: 1.1;
  }
  .contact-list {
    list-style: none;
    margin-top: 10px;
  }
  .contact-list li {
    display: flex;
    align-items: center;
    font-size: 15.5px;
    font-weight: 500;
    height: 23px;
    white-space: nowrap;
  }
  .contact-icon {
    width: 13px;
    height: 13px;
    margin-right: 12px;
    fill: var(--green);
    flex: none;
  }
  .footer-band {
    position: absolute;
    left: 0;
    bottom: 0;
    width: 806px;
    height: 130px;
    background: linear-gradient(180deg, var(--green) 0%, var(--green-deep) 100%);
  }
</style>
</head>
<body>
  <main class="letterhead">
    <div class="brand-name">HARBORKEY</div>

    <section class="contact-block">
      <p class="contact-name">GARETH LINDQVIST</p>
      <p class="contact-role">Operations Manager</p>
      <ul class="contact-list">
        <li>
          <svg class="contact-icon" viewBox="0 0 16 16" aria-hidden="true"><path d="M3.5 1.5l2.3 2.8-1.4 1.6c.9 2 2.7 3.8 4.7 4.7l1.6-1.4 2.8 2.3-1.3 2.5C7 14 2 9 1 2.8z"/></svg>
          1 (555) 384-2917
        </li>
        <li>
          <svg class="contact-icon" viewBox="0 0 16 16" aria-hidden="true"><path d="M1 3.5h14v9H1z M1.5 4l6.5 5 6.5-5" stroke="#fff" stroke-width="1"/></svg>
          Gareth@harborkey-example.ca
        </li>
        <li>
          <svg class="contact-icon" viewBox="0 0 16 16" aria-hidden="true"><circle cx="8" cy="8" r="7"/><path d="M1 8h14M8 1c-3 3-3 11 0 14M8 1c3 3 3 11 0 14" stroke="#fff" stroke-width="1" fill="none"/></svg>
          Harborkey-example.ca
        </li>
      </ul>
    </section>

    <div class="footer-band" role="img" aria-label="Decorative footer band in brand green and black"></div>
  </main>
</body>
</html>
```